Construction Company

Design a clutter free business card, it can be double-sided utilizing the logo for VKM Ltd simple with all relevant contact information.

Please also a letterhead design to function for the purposes of invoicing, all mail requirements, with header to be distinctive while the footer ties page together and incorporates all necessary information.

For now, please use generic / dummy text and when a winner is selected, I will disclose the contact information.

Hi Designers! Please read the updated brief which includes the design of a business card and letterhead. Thank you!

```html
<!DOCTYPE html>
<html lang="en">
<head>
<meta charset="utf-8">
<title>VKM Ltd Business Card</title>
<link rel="stylesheet" href="https://fonts.googleapis.com/css2?family=Roboto:wght@400;500&display=swap">
<style>
  :root {
    --page-bg: #d9d9db;
    --card-bg: #3b3b3d;
    --card-edge: #c9a227;
    --gold: #d4a82a;
    --text-light: #ececec;
    --mark-tone: #4a4a4d;
  }
  * { box-sizing: border-box; margin: 0; padding: 0; }
  html, body { width: 1200px; height: 899px; overflow: hidden; }
  body {
    background: var(--page-bg);
    font-family: "Roboto", Arial, sans-serif;
    display: flex;
    flex-direction: column;
    align-items: center;
    justify-content: center;
    gap: 44px;
  }
  .card {
    position: relative;
    width: 640px;
    height: 366px;
    background: var(--card-bg);
    border-left: 4px solid var(--card-edge);
    border-bottom: 4px solid var(--card-edge);
    overflow: hidden;
  }
  .card-front {
    display: flex;
    flex-direction: column;
    align-items: center;
    justify-content: center;
  }
  .brand {
    display: flex;
    align-items: center;
    gap: 16px;
  }
  .brand-dot {
    width: 30px;
    height: 30px;
    border-radius: 50%;
    background: var(--gold);
  }
  .brand-name {
    font-size: 58px;
    font-weight: 500;
    color: var(--gold);
    letter-spacing: 2px;
  }
  .front-website {
    margin-top: 34px;
    font-size: 17px;
    color: var(--text-light);
    letter-spacing: 0.5px;
  }
  .back-mark {
    position: absolute;
    right: -50px;
    top: -30px;
    width: 300px;
    height: 300px;
    border-radius: 50%;
    background: var(--mark-tone);
  }
  .contact {
    position: absolute;
    left: 56px;
    top: 70px;
    color: var(--text-light);
  }
  .person-name {
    font-size: 24px;
    font-weight: 500;
    color: var(--gold);
  }
  .person-role {
    font-size: 16px;
    margin-top: 4px;
  }
  .address {
    margin-top: 46px;
    font-size: 16px;
    line-height: 1.3;
  }
  .contact-list {
    list-style: none;
    margin-top: 40px;
    font-size: 16px;
  }
  .contact-list li {
    display: flex;
    align-items: center;
    gap: 12px;
    margin-bottom: 6px;
  }
  .contact-list svg { width: 15px; height: 15px; flex: none; }
</style>
</head>
<body>
  <section class="card card-front">
    <div class="brand">
      <span class="brand-dot"></span>
      <span class="brand-name">VKM Ltd</span>
    </div>
    <p class="front-website">www.vkmltd.example</p>
  </section>

  <section class="card card-back">
    <div class="back-mark"></div>
    <div class="contact">
      <h1 class="person-name">Daniel Reyes</h1>
      <p class="person-role">Manager</p>
      <p class="address">14 Harbor Lane<br>Milford, ZIP 4821</p>
      <ul class="contact-list">
        <li>
          <svg viewBox="0 0 16 16" aria-hidden="true"><path fill="#d4a82a" d="M3.5 1.5l2.5 0 1 3.5-1.6 1.2a9 9 0 0 0 4.4 4.4L11 9l3.5 1v2.5c0 1-1 2-2 2A11 11 0 0 1 1.5 3.5c0-1 1-2 2-2z"/></svg>
          555-318-7742
        </li>
        <li>
          <svg viewBox="0 0 16 16" aria-hidden="true"><rect x="1.5" y="3.5" width="13" height="9" fill="none" stroke="#d4a82a" stroke-width="1.5"/><path d="M1.5 3.5l6.5 5 6.5-5" fill="none" stroke="#d4a82a" stroke-width="1.5"/></svg>
          info@vkmltd.example
        </li>
        <li>
          <svg viewBox="0 0 16 16" aria-hidden="true"><circle cx="8" cy="8" r="6.5" fill="none" stroke="#d4a82a" stroke-width="1.5"/><path d="M1.5 8h13M8 1.5c-3 3.5-3 9.5 0 13M8 1.5c3 3.5 3 9.5 0 13" fill="none" stroke="#d4a82a" stroke-width="1.2"/></svg>
          www.vkmltd.example
        </li>
      </ul>
    </div>
  </section>
</body>
</html>
```